Emergency Dental Referral Company

I need a brochure to advertise my business to prospective dentists that may want to join or to dentists that may want to use this for their own patients. I also need to advertise this brochure to ER physicians who see many dental emergencies. This brochure is meant to be dual purpose: advertise our company and services to the ER physicians who then hand out the brochures to the dental emergency patients in pain. See our website for further details at www.vellumcrestora.com

I will also be attaching our logo design.

Target Market(s)

Emergency Room physicians and other medical personnel who will distribute these brochures to patients in dental pain and dental emergencies

Industry/Entity Type

Business

Font styles to use
Serif
Sans Serif

Requirements
Must have
• Must be simple! Must have a call to action- inspiration to go to website. Highlight our guarantee that states "If you are not seen by a dentist in 24 hours or less, you will receive your money back. Emphasis on the logo. Must discuss how we find a dentist in your zip code in three easy steps.
• For the color- please make similar to our website of www.vellumcrestora.com
Nice to have
• Would like to state that this service can see patients at any hour of the day.
Should not have
• no contact information besides the URL. www.vellumcrestora.com

```html
<!DOCTYPE html>
<html lang="en">
<head>
<meta charset="utf-8">
<title>Vellum Crestora – Brochure Front</title>
<link rel="stylesheet" href="https://fonts.googleapis.com/css2?family=Arimo:wght@400&family=Oswald:wght@300;400;500;600;700&display=swap">
<style>
  :root {
    --ink-dark: #3a3a3c;
    --ink-text: #333335;
    --paper: #ffffff;
    --accent-green: #3dbb4d;
    --heading-font: 'Oswald', 'Arial Narrow', sans-serif;
    --body-font: 'Arimo', 'Helvetica', sans-serif;
  }

  html, body {
    margin: 0;
    padding: 0;
    width: 1200px;
    height: 857px;
    overflow: hidden;
    background: var(--paper);
  }

  .brochure {
    position: relative;
    width: 1200px;
    height: 857px;
    overflow: hidden;
    font-family: var(--body-font);
  }

  .brochure__shapes {
    position: absolute;
    inset: 0;
    width: 1200px;
    height: 857px;
    display: block;
  }

  .copy {
    position: absolute;
    margin: 0;
  }

  .section-title {
    font-family: var(--heading-font);
    font-weight: 400;
    text-transform: uppercase;
    line-height: 29px;
    font-size: 26px;
    letter-spacing: -0.2px;
  }

  .body-text p {
    margin: 0 0 17px 0;
    font-size: 12.6px;
    line-height: 17px;
  }

  /* Intro panel (top left) */
  .intro__title {
    left: 34px;
    top: 30px;
    color: var(--paper);
  }
  .intro__body {
    left: 33px;
    top: 81px;
    width: 536px;
    color: var(--paper);
  }

  /* Brand title (top right) */
  .brand-title {
    right: 38px;
    top: 40px;
    font-family: var(--heading-font);
    font-weight: 700;
    font-size: 66px;
    line-height: 64px;
    text-align: right;
    text-transform: uppercase;
    color: var(--ink-text);
    letter-spacing: -0.5px;
  }

  /* Steps badge */
  .steps-badge {
    left: 750px;
    top: 275px;
    transform: translate(-50%, -50%);
    text-align: center;
    color: var(--paper);
    font-family: var(--heading-font);
    text-transform: uppercase;
    line-height: 44px;
  }
  .steps-badge__count {
    display: block;
    font-weight: 600;
    font-size: 46px;
  }
  .steps-badge__label {
    display: block;
    font-weight: 300;
    font-size: 46px;
  }

  /* Lower left panel */
  .info-left__title {
    left: 34px;
    top: 519px;
    color: var(--ink-text);
  }
  .info-left__title .indent { padding-left: 34px; }
  .info-left__body {
    left: 33px;
    top: 587px;
    width: 536px;
    color: var(--ink-text);
  }

  /* Lower right panel */
  .info-right__title {
    left: 636px;
    top: 519px;
    color: var(--paper);
  }
  .info-right__title .indent { padding-left: 40px; }
  .info-right__body {
    left: 635px;
    top: 587px;
    width: 536px;
    color: var(--paper);
  }
</style>
</head>
<body>
<main class="brochure">

  <svg class="brochure__shapes" viewBox="0 0 1052 744" preserveAspectRatio="none" xmlns="http://www.w3.org/2000/svg">
    <defs>
      <linearGradient id="tone-room" x1="0" y1="0" x2="1" y2="1">
        <stop offset="0" stop-color="#f4f6f5"/>
        <stop offset="0.55" stop-color="#dfe6dc"/>
        <stop offset="1" stop-color="#c6d6bf"/>
      </linearGradient>
      <linearGradient id="tone-instruments" x1="0" y1="0" x2="1" y2="1">
        <stop offset="0" stop-color="#c2b275"/>
        <stop offset="1" stop-color="#6d6a3e"/>
      </linearGradient>
      <linearGradient id="tone-hand" x1="0" y1="0" x2="0" y2="1">
        <stop offset="0" stop-color="#bdb8d4"/>
        <stop offset="0.5" stop-color="#c48a72"/>
        <stop offset="1" stop-color="#a45f4c"/>
      </linearGradient>
      <linearGradient id="tone-files" x1="0" y1="0" x2="0" y2="1">
        <stop offset="0" stop-color="#e0d3b8"/>
        <stop offset="0.5" stop-color="#cf8f6a"/>
        <stop offset="1" stop-color="#3f88b5"/>
      </linearGradient>
      <linearGradient id="tone-teeth" x1="0" y1="0" x2="1" y2="1">
        <stop offset="0" stop-color="#eedada"/>
        <stop offset="1" stop-color="#c7808a"/>
      </linearGradient>
      <linearGradient id="tone-dentist" x1="0" y1="0" x2="0" y2="1">
        <stop offset="0" stop-color="#e9e6e1"/>
        <stop offset="0.45" stop-color="#d9c39e"/>
        <stop offset="1" stop-color="#f3f3f3"/>
      </linearGradient>
      <linearGradient id="tone-assistant" x1="0" y1="0" x2="0" y2="1">
        <stop offset="0" stop-color="#ece8e4"/>
        <stop offset="0.5" stop-color="#d7b49c"/>
        <stop offset="1" stop-color="#4aa6c2"/>
      </linearGradient>
    </defs>

    <rect class="panel-ground panel-ground--left" x="0" y="0" width="526" height="744" fill="var(--paper)"/>
    <rect class="panel-ground panel-ground--right" x="526" y="0" width="526" height="744" fill="var(--ink-dark)"/>

    <rect class="photo photo--clinic" x="526" y="0" width="526" height="504" fill="url(#tone-room)"
          role="img" aria-label="Photo of a bright dental treatment room with a green patient chair"/>

    <polygon class="band band--intro" fill="var(--ink-dark)"
             points="0,0 547,0 658,111 527,242 396,373 265,242 134,373 0,239"/>

    <polygon class="band band--lower-right" fill="var(--ink-dark)"
             points="526,504 658,373 789,504 920,373 1051,504 1052,503 1052,744 526,744"/>

    <polygon class="photo photo--instruments" fill="url(#tone-instruments)"
             points="0,239 134,373 0,507"
             role="img" aria-label="Photo of sterilised dental scissors and instruments"/>
    <polygon class="photo photo--hand" fill="url(#tone-hand)"
             points="265,242 396,373 265,504 134,373"
             role="img" aria-label="Photo of an open hand holding a pain relief capsule"/>
    <polygon class="photo photo--files" fill="url(#tone-files)"
             points="526,242 396,373 526,504"
             role="img" aria-label="Photo of colourful root canal files in a holder"/>
    <polygon class="photo photo--teeth" fill="url(#tone-teeth)"
             points="526,242 658,373 526,504"
             role="img" aria-label="Photo of a dental teeth model"/>
    <polygon class="photo photo--dentist" fill="url(#tone-dentist)"
             points="789,242 920,373 789,504 658,373"
             role="img" aria-label="Photo of a smiling dentist in a white coat with a stethoscope"/>
    <polygon class="photo photo--assistant" fill="url(#tone-assistant)"
             points="1051,242 1052,243 1052,503 1051,504 920,373"
             role="img" aria-label="Photo of a dental nurse in blue scrubs holding an apple"/>

    <polygon class="steps-badge__shape" fill="var(--accent-green)"
             points="658,111 789,242 658,373 527,242"/>
  </svg>

  <h2 class="copy section-title intro__title">Seen by a dentist within 24 hours</h2>
  <div class="copy body-text intro__body">
    <p>A dental emergency rarely waits for office hours. Vellum Crestora connects patients in tooth pain with a trusted local dentist who can see them fast, often the same day. We work alongside emergency rooms, urgent care teams and dentists to turn a painful night into a clear next step.</p>
    <p>For ER physicians and medical staff: many patients you treat for dental pain need a dentist, not a hospital bed. Hand this brochure to them before discharge. Our service is open at any hour of the day or night, so patients can request care the moment they leave your department. For dentists: join our referral network to welcome new patients in your area, or use the service to place your own patients when your schedule is full.</p>
  </div>

  <h1 class="copy brand-title">Vellum<br>Crestora</h1>

  <p class="copy steps-badge">
    <span class="steps-badge__count">3 Easy</span>
    <span class="steps-badge__label">Steps</span>
  </p>

  <h2 class="copy section-title info-left__title"><span class="indent">How it</span><br>works for you</h2>
  <div class="copy body-text info-left__body">
    <p>Finding a dentist in your zip code takes only three easy steps. Everything starts online at www.vellumcrestora.com and no phone calls are needed. The service is open at any hour of the day, seven days a week, including holidays.</p>
    <p>Step one: visit our website and enter your zip code so we can search the dentists closest to you. Step two: tell us briefly about your pain, swelling or broken tooth and choose the time that suits you best. Step three: we match you with a dentist in your zip code and confirm your visit, with the address and time sent straight to you. Bring this brochure, a photo ID and a list of any medicines you take. Our partner dentists treat toothaches, infections, lost fillings, cracked teeth and other urgent problems, so you get relief from a professional who can fix the cause.</p>
  </div>

  <h2 class="copy section-title info-right__title"><span class="indent">Our 24 hour</span><br>guarantee</h2>
  <div class="copy body-text info-right__body">
    <p>We stand behind every referral with a simple promise: if you are not seen by a dentist in 24 hours or less, you will receive your money back. No forms to argue over and no fine print to decode. We keep this promise by working with a growing network of licensed dentists who set aside time for urgent visits and who share our belief that nobody should wait days in pain. Patients sent to us from an emergency room are placed as a priority, and our team follows each request until the visit is booked. Dentists who join gain new patients from their own area, while physicians gain a reliable place to send people who need dental care.</p>
    <p>Do not wait for the pain to get worse. Visit www.vellumcrestora.com now, enter your zip code and let us find a dentist who can see you within 24 hours, at any hour of the day or night. Seen fast, or your money back.</p>
  </div>

</main>
</body>
</html>
```